Letterhead for a German Distribution/Manufacturing Company

We need a professional Letterhead in a unique Design.
not to playful.
The Letterhead has to show show that we are a international company with headquater in Nordland.
all details like adress, Vat Tax Number, Bank Accout, Eori, email, Company number has to be on the Letterhead.
for example use: VAT TAX DE5470318 Bank Account: Kestrel Bank IBAN DE412058731ß204683 Swift: MORV0417352 EORI 3150428697 Company Number: HRB 51806 Adress: VOLMINTA UG Ahornweg 7 Postal Code 06384 City Kesselbrunn Country: Nordland Email: info@volminta-example.com
the design can be colored but doesnt have to be
Industry/Entity Type
Manufacturing and international distribution
Requirements
Must have
- show that we are a international company with headquater in Nordland. our company infos and logo

```html
<!DOCTYPE html>
<html lang="en">
<head>
<meta charset="utf-8">
<title>VOLMINTA Letterhead</title>
<link href="https://fonts.googleapis.com/css2?family=Mulish:wght@500&family=Arimo:wght@400;500&display=swap" rel="stylesheet">
<style>
  :root {
    --backdrop: #3a2a20;
    --paper: #ffffff;
    --paper-shade: #ececee;
    --ink: #454545;
    --ink-soft: #5a5a5a;
  }
  html, body {
    margin: 0;
    padding: 0;
    width: 1084px;
    height: 1200px;
    overflow: hidden;
    background: var(--backdrop);
  }
  .letterhead {
    position: absolute;
    left: 102px;
    top: 28px;
    width: 880px;
    height: 1143px;
    background:
      linear-gradient(180deg, var(--paper) 0%, var(--paper-shade) 33.2%, var(--paper) 33.4%, var(--paper-shade) 66.6%, var(--paper) 66.8%, var(--paper-shade) 100%);
    box-shadow: 0 6px 18px rgba(0,0,0,0.45);
    font-family: "Arimo", Arial, sans-serif;
    color: var(--ink);
  }
  .brand {
    position: absolute;
    left: 86px;
    top: 62px;
    display: flex;
    align-items: center;
    gap: 14px;
  }
  .brand-dot {
    width: 30px;
    height: 30px;
    border-radius: 50%;
    background: var(--ink);
  }
  .brand-name {
    font-family: "Mulish", sans-serif;
    font-weight: 500;
    font-size: 40px;
    letter-spacing: 0.5px;
    color: var(--ink);
  }
  .address, .contact {
    position: absolute;
    top: 66px;
    font-size: 13px;
    line-height: 18px;
    color: var(--ink-soft);
    margin: 0;
    font-style: normal;
  }
  .address { left: 440px; }
  .contact { left: 632px; list-style: none; padding: 0; }
  .contact li { display: flex; align-items: center; gap: 8px; }
  .contact svg { width: 12px; height: 12px; fill: var(--ink); flex: none; }
  .legal {
    position: absolute;
    left: 0;
    right: 0;
    top: 1058px;
    text-align: center;
    font-size: 13px;
    line-height: 22px;
    font-weight: 500;
    color: var(--ink-soft);
  }
  .legal p { margin: 0; }
</style>
</head>
<body>
  <main class="letterhead">
    <header>
      <div class="brand">
        <span class="brand-dot"></span>
        <span class="brand-name">VOLMINTA</span>
      </div>
      <address class="address">
        VOLMINTA UG<br>
        Ahornweg 7 06384<br>
        City Kesselbrunn Nordland
      </address>
      <ul class="contact">
        <li>
          <svg viewBox="0 0 12 12" aria-hidden="true"><path d="M1 4c0-2 2-3 5-3s5 1 5 3v1H8V4H4v1H1zM3 6h6l2 5H1z"/></svg>
          555.014.2730
        </li>
        <li>
          <svg viewBox="0 0 12 12" aria-hidden="true"><path d="M0 3h12v1L6 7 0 4zM0 5l6 3 6-3v5H0z"/></svg>
          info@volminta-example.com
        </li>
        <li>
          <svg viewBox="0 0 12 12" aria-hidden="true"><circle cx="6" cy="6" r="5.5"/><path d="M3 4h3v2H4zM7 7h2v2H7z" fill="#fff"/></svg>
          www.volminta-example.com
        </li>
      </ul>
    </header>
    <footer class="legal">
      <p>VAT TAX DE5470318 | Bank Account: Kestrel Bank IBAN DE412058731ß204683</p>
      <p>Swift: MORV0417352 EORI 3150428697 | Company Number: HRB 51806</p>
    </footer>
  </main>
</body>
</html>
```